Construction Company Cellar Crafters needs Business Card

I would like modern looking business card design. I am attaching logo of our company. Please include cell nr 302.418.7650 , email address cellarcrafters4u@examplemail.com, web : cellarcrafters4u.com, please also include wording: Specializing in finishing and remodeling basements. You can play with dark grey and orange colors or any ideas are welcome. Also include social media icons Friendloop and HouseGuidr.

```html
<!DOCTYPE html>
<html lang="en">
<head>
<meta charset="UTF-8">
<title>Cellar Crafters — Business Card</title>
<link rel="stylesheet" href="https://fonts.googleapis.com/css2?family=Oxanium:wght@500&family=Open+Sans:wght@400&display=swap">
<style>
  :root {
    --page-bg: #e6e4e1;
    --card-bg: #f7f6f4;
    --panel-black: #0b0b0b;
    --accent-orange: #f15a24;
    --text-dark: #1e1e1e;
    --text-light: #ffffff;
    --chip-grey: #5b6770;
  }
  * { margin: 0; padding: 0; box-sizing: border-box; }
  html, body {
    width: 1200px; height: 900px; overflow: hidden;
    background: var(--page-bg);
  }
  .canvas {
    position: relative; width: 1200px; height: 900px;
  }
  .card {
    position: absolute; left: 150px; top: 171px;
    width: 900px; height: 558px;
    background: var(--card-bg);
    overflow: hidden;
    box-shadow: 0 10px 30px rgba(0,0,0,0.18);
  }
  .card-panel {
    position: absolute; inset: 0;
    width: 900px; height: 558px;
  }
  .tagline {
    position: absolute; left: 51px; top: 236px;
    font-family: "Oxanium", sans-serif; font-weight: 500;
    font-size: 23px; line-height: 37px; letter-spacing: 1.5px;
    text-transform: uppercase;
    color: var(--accent-orange);
  }
  .contact-list {
    position: absolute; left: 51px; top: 406px;
    list-style: none;
    font-family: "Open Sans", sans-serif;
    font-size: 22px; line-height: 32px;
    color: var(--text-light);
  }
  .contact-list li { display: flex; align-items: center; gap: 8px; }
  .contact-icon { width: 14px; height: 14px; flex: none; }
  .brand-name {
    position: absolute; right: 44px; top: 160px;
    font-family: "Oxanium", sans-serif; font-weight: 500;
    font-size: 44px; letter-spacing: 1px;
    text-transform: uppercase;
    color: var(--accent-orange);
  }
  .person {
    position: absolute; right: 44px; top: 322px; text-align: right;
  }
  .person-name {
    font-family: "Oxanium", sans-serif; font-weight: 500;
    font-size: 28px; letter-spacing: 3px;
    text-transform: uppercase;
    color: var(--accent-orange);
  }
  .person-title {
    margin-top: 4px;
    font-family: "Open Sans", sans-serif;
    font-size: 21px; color: var(--text-dark);
  }
  .social-list {
    position: absolute; right: 44px; top: 470px;
    display: flex; gap: 26px; list-style: none;
    font-family: "Open Sans", sans-serif; font-size: 18px;
    color: var(--text-dark);
  }
  .social-list li { display: flex; align-items: center; gap: 8px; }
  .social-chip { width: 22px; height: 22px; background: var(--chip-grey); }
  .social-chip.is-orange { background: var(--accent-orange); }
</style>
</head>
<body>
<div class="canvas">
  <div class="card">
    <svg class="card-panel" viewBox="0 0 900 558" aria-hidden="true">
      <polygon points="0,0 51,0 636,558 0,558" fill="var(--panel-black)"/>
      <polygon points="51,0 59,0 646,558 636,558" fill="var(--accent-orange)"/>
    </svg>

    <p class="tagline">Specializing<br>in finishing<br>and remodeling<br>basements.</p>

    <ul class="contact-list">
      <li>
        <svg class="contact-icon" viewBox="0 0 14 14"><rect x="3.5" y="0.5" width="7" height="13" rx="1.5" fill="none" stroke="var(--accent-orange)" stroke-width="1.6"/><rect x="6" y="10.5" width="2" height="1.5" fill="var(--accent-orange)"/></svg>
        302.418.7650
      </li>
      <li>
        <svg class="contact-icon" viewBox="0 0 14 14"><circle cx="7" cy="7" r="6" fill="none" stroke="var(--accent-orange)" stroke-width="1.5"/><ellipse cx="7" cy="7" rx="2.6" ry="6" fill="none" stroke="var(--accent-orange)" stroke-width="1.2"/><line x1="1" y1="7" x2="13" y2="7" stroke="var(--accent-orange)" stroke-width="1.2"/></svg>
        cellarcrafters4u.com
      </li>
      <li>
        <svg class="contact-icon" viewBox="0 0 14 14"><rect x="0.5" y="2.5" width="13" height="9" fill="var(--accent-orange)"/><polyline points="0.5,2.5 7,8 13.5,2.5" fill="none" stroke="var(--panel-black)" stroke-width="1.2"/></svg>
        cellarcrafters4u@examplemail.com
      </li>
    </ul>

    <div class="brand-name">Cellar Crafters</div>

    <div class="person">
      <div class="person-name">Daniel Hart</div>
      <div class="person-title">Managing Director</div>
    </div>

    <ul class="social-list">
      <li><span class="social-chip"></span>Friendloop</li>
      <li><span class="social-chip is-orange"></span>HouseGuidr</li>
    </ul>
  </div>
</div>
</body>
</html>
```